Ledgerwise Forge - WordPress Theme & Logo

Design a logo and Wordpress website design for Ledgerwise Forge. Ledgerwise Forge provides cryptocurrency development services to clients who need a team to create & continue developing a new cryptocurrency or who want to replace their current cryptocurrency development team. more details in the attached document.
Updates

Target Market(s)

Entrepreneurs who are building a business / platform that makes use of an underlying cryptocurrency.

Logo Text

LF or Ledgerwise Forge

Coding

Coded - Design and coding required

Font styles to use
Sans Serif

Requirements
Must have
• Professional logo, complete coded Wordpress theme for all pages, containing all specified links and buttons
Nice to have
• It would be nice if the buttons that are meant to integrate with Dealtrail contain the necessary code for that. I can provide any necessary Dealtrail details from my account.
Should not have
• Slow loading time

```html
<!DOCTYPE html>
<html lang="en">
<head>
<meta charset="utf-8">
<title>Ledgerwise Forge – Cryptocurrency Development</title>
<link rel="stylesheet" href="https://fonts.googleapis.com/css2?family=Montserrat:wght@600;700;800&family=Open+Sans:wght@400;600;700&display=swap">
<style>
:root{
  --navy:#0b1630;
  --navy-deep:#060d1f;
  --blue:#1a73e8;
  --blue-bright:#2f80ff;
  --band:#1d3b6b;
  --hex:#1f4f95;
  --ink:#111a2b;
  --muted:#5d6676;
  --line:#e4e8ef;
  --soft:#f3f5f8;
  --white:#ffffff;
}
*{box-sizing:border-box;margin:0;padding:0}
html,body{width:1200px;height:3348px;overflow:hidden}
body{font-family:"Open Sans",Arial,sans-serif;color:var(--ink);background:var(--white)}
h1,h2,h3,.brand,.btn,.label,.nav a{font-family:"Montserrat",Arial,sans-serif}
.btn{display:inline-block;background:var(--blue);color:var(--white);font-weight:700;font-size:14px;border-radius:30px;padding:14px 30px;text-decoration:none}
.label{display:block;font-size:9px;letter-spacing:1px;color:var(--blue);font-weight:700;text-transform:uppercase;text-align:center;margin-top:6px}
.mini-hex{display:block;margin:0 auto}
.section-title{font-size:40px;font-weight:800;text-align:center;color:var(--ink);margin-top:8px}

/* hero */
.hero{position:relative;height:680px;background:linear-gradient(100deg,#0a1530 0%,#0d1c3e 55%,#0a1430 100%);color:var(--white);overflow:hidden}
.hero-visual{position:absolute;left:0;top:0;width:640px;height:680px;background:radial-gradient(ellipse at 45% 40%,#2c3f66 0%,#15254a 45%,rgba(10,21,48,0) 80%)}
.topbar{position:absolute;left:0;top:0;width:1200px;height:88px;display:flex;align-items:center;padding:0 80px;z-index:2}
.brand{display:flex;align-items:center;gap:10px;color:var(--white);font-weight:800;font-size:20px}
.brand-mark{width:30px;height:30px;background:var(--white);border-radius:4px}
.nav{margin-left:auto;display:flex;align-items:center;gap:26px}
.nav a{color:var(--white);font-size:13px;font-weight:700;text-decoration:none}
.flag{width:24px;height:16px;background:linear-gradient(#c8102e 0 0) center/100% 4px no-repeat,linear-gradient(#c8102e 0 0) center/4px 100% no-repeat,#1d3f8f}
.nav .btn{padding:12px 22px;font-size:13px}
.hero-copy{position:absolute;left:680px;top:170px;width:440px}
.hero-copy h1{font-size:34px;line-height:1.2;font-weight:800;text-transform:uppercase}
.hero-copy p{font-size:13px;line-height:1.7;color:#c9d3e6;margin:18px 0 30px}
.slider{position:absolute;left:80px;top:560px;display:flex;align-items:center;gap:60px}
.slider .next{font-size:16px;display:flex;align-items:center;gap:12px}
.slider .count{font-family:"Montserrat",Arial,sans-serif;font-size:54px;font-weight:800}
.slider .count span{font-size:20px;color:#8aa0c6}

/* why */
.why{height:520px;padding-top:40px}
.why-cards{display:flex;justify-content:center;gap:30px;margin-top:34px}
.why-card{width:320px;height:264px;border:1px solid var(--line);box-shadow:0 4px 18px rgba(20,40,80,.08);text-align:center;padding-top:34px}
.why-card h3{font-size:24px;font-weight:800;margin:20px 0 10px}
.why-card p{font-size:13px;color:var(--muted);line-height:1.6;padding:0 40px}

/* who */
.who{position:relative;height:480px;background:linear-gradient(90deg,#1a3566,#1e4178 60%,#1a3566)}
.who-visual{position:absolute;left:100px;top:72px;width:452px;height:336px;background:linear-gradient(135deg,#6d7b93,#2d3b57 55%,#c59a55)}
.who-copy{position:absolute;left:628px;top:110px;width:470px;color:var(--white)}
.who-copy .label{text-align:left;color:#bcd0f2;margin:0}
.who-copy h2{font-size:42px;font-weight:800;margin:4px 0 14px}
.who-copy p{font-size:13px;line-height:1.75;color:#d6e0f2;margin-bottom:26px}
.who-copy .btn{padding:12px 26px;font-size:13px}

/* testimonials */
.testimonials{height:500px;background:var(--soft);padding-top:72px}
.quotes{display:flex;justify-content:center;gap:22px;margin-top:30px}
.quote{position:relative;width:340px;height:270px;background:var(--white);box-shadow:0 4px 18px rgba(20,40,80,.08);text-align:center;padding-top:18px}
.avatar{width:56px;height:56px;border-radius:50%;margin:0 auto;background:linear-gradient(135deg,#d6dbe4,#8e9ab0)}
.stars{color:#f3b400;font-size:11px;letter-spacing:2px;margin-top:6px}
.quote h3{font-size:10px;font-weight:800;color:var(--blue);margin-top:2px;letter-spacing:.5px}
.quote p{font-size:12px;line-height:1.6;color:var(--muted);padding:10px 34px 0}
.quote-badge{position:absolute;left:50%;bottom:-22px;margin-left:-22px;width:44px;height:44px;border-radius:50%;background:var(--hex);display:flex;align-items:center;justify-content:center}

/* what */
.what{height:684px;padding-top:72px}
.what-intro{width:940px;margin:16px auto 0;font-size:13px;line-height:1.75;color:var(--muted);text-align:center}
.plans{display:flex;justify-content:center;gap:30px;margin-top:36px}
.plan{width:320px;height:312px;border:1px solid var(--line);box-shadow:0 4px 18px rgba(20,40,80,.08);text-align:center;padding-top:24px}
.plan h3{font-size:22px;font-weight:800;line-height:1.2;margin-top:14px;min-height:54px;display:flex;align-items:center;justify-content:center}
.plan ul{list-style:none;text-align:left;width:150px;margin:12px auto 18px}
.plan li{font-size:13px;color:var(--ink);display:flex;align-items:center;gap:8px;margin-bottom:8px}
.tick{width:14px;height:14px;border-radius:50%;background:var(--blue);display:inline-flex;align-items:center;justify-content:center;flex:none}
.plan .btn{padding:11px 32px;font-size:13px}

/* footer */
.footer{position:relative;height:484px;background:var(--navy);color:var(--white)}
.footer-brand{position:absolute;left:110px;top:70px;width:260px}
.footer-brand .brand{font-size:26px;gap:14px}
.footer-brand .brand-mark{width:64px;height:64px;border-radius:6px}
.socials{display:flex;gap:10px;margin-top:22px;padding-left:78px}
.socials span{width:22px;height:22px;border-radius:3px;background:var(--white)}
.footer-col{position:absolute;top:70px}
.footer-col h4{font-family:"Montserrat",Arial,sans-serif;font-size:15px;font-weight:700;margin-bottom:14px}
.footer-col a{display:block;color:#d2d9e6;text-decoration:none;font-size:13px;margin-bottom:8px}
.newsletter input{display:block;width:240px;height:38px;border:0;border-radius:20px;padding:0 16px;font-size:13px;font-family:"Open Sans",Arial,sans-serif;margin-bottom:12px}
.newsletter .btn{width:240px;text-align:center;padding:11px 0;font-size:13px}
.copyright{position:absolute;left:0;bottom:0;width:1200px;height:44px;line-height:44px;background:var(--navy-deep);text-align:center;font-size:12px;color:#c3cbda}
</style>
</head>
<body>

<header class="hero">
  <div class="hero-visual" role="img" aria-label="Hand holding a smartphone showing a trading chart over a dark city backdrop"></div>
  <div class="topbar">
    <div class="brand"><span class="brand-mark"></span>Ledgerwise Forge</div>
    <nav class="nav">
      <a href="#about">ABOUT US</a>
      <a href="#services">OUR SERVICES</a>
      <a href="#testimonials">TESTIMONIALS</a>
      <a href="#blog">BLOG</a>
      <span class="flag" aria-label="English"></span>
      <a class="btn" href="#consult">Schedule a Free Consultation</a>
    </nav>
  </div>
  <div class="hero-copy">
    <h1>Your own cryptocurrency. Secure, easy to use, and built by an expert team.</h1>
    <p>Ledgerwise Forge works with founders to plan, build and launch a dedicated cryptocurrency. We handle everything from design and audits to wallets and ongoing support, so your team can stay focused on growing the platform around your coin.</p>
    <a class="btn" href="#consult">Schedule a Free Consultation</a>
  </div>
  <div class="slider">
    <div class="next">Next
      <svg width="22" height="12" viewBox="0 0 22 12"><path d="M0 6h20M15 1l5 5-5 5" stroke="#fff" stroke-width="1.5" fill="none"/></svg>
    </div>
    <div class="count">01/<span>03</span></div>
  </div>
</header>

<section class="why">
  <svg class="mini-hex" width="26" height="28" viewBox="0 0 26 28"><path d="M13 1l11 6.5v13L13 27 2 20.5v-13z" fill="#1f4f95"/></svg>
  <span class="label">Why choose us</span>
  <h2 class="section-title">Why choose Ledgerwise Forge</h2>
  <div class="why-cards">
    <div class="why-card">
      <svg width="76" height="84" viewBox="0 0 76 84"><path d="M38 2l34 20v40L38 82 4 62V22z" fill="#1f4f95"/><path d="M26 36h24l-12 16z M26 36l5-7h14l5 7" stroke="#fff" stroke-width="2.5" fill="none" stroke-linejoin="round"/></svg>
      <h3>Value</h3>
      <p>A team of experts, regular updates, and fixed costs</p>
    </div>
    <div class="why-card">
      <svg width="76" height="84" viewBox="0 0 76 84"><path d="M38 2l34 20v40L38 82 4 62V22z" fill="#1f4f95"/><path d="M26 46v-6a12 12 0 0124 0v6" stroke="#fff" stroke-width="2.5" fill="none"/><rect x="23" y="43" width="6" height="10" rx="2" fill="#fff"/><rect x="47" y="43" width="6" height="10" rx="2" fill="#fff"/></svg>
      <h3>Support</h3>
      <p>Receive advice and other services, beyond development.</p>
    </div>
    <div class="why-card">
      <svg width="76" height="84" viewBox="0 0 76 84"><path d="M38 2l34 20v40L38 82 4 62V22z" fill="#1f4f95"/><path d="M22 40l8-6 8 5 8-5 8 6-12 10h-8z" stroke="#fff" stroke-width="2.5" fill="none" stroke-linejoin="round"/></svg>
      <h3>Commitment</h3>
      <p>Enjoy regular updates and new features</p>
    </div>
  </div>
</section>

<section class="who" id="about">
  <div class="who-visual" role="img" aria-label="Business people exchanging a phone with glowing network icons"></div>
  <div class="who-copy">
    <span class="label">About us</span>
    <h2>Who We Are</h2>
    <p>In addition to creating and enhancing cryptocurrencies for clients, the Ledgerwise Forge team has been running the Nordvale cryptocurrency since 2017. We pride ourselves on long-term relationships, enabling us to deliver the very highest quality and giving you peace of mind that you've got a professional and trustworthy team at your side.</p>
    <a class="btn" href="#about">Learn More</a>
  </div>
</section>

<section class="testimonials" id="testimonials">
  <svg class="mini-hex" width="26" height="28" viewBox="0 0 26 28"><path d="M13 1l11 6.5v13L13 27 2 20.5v-13z" fill="#1f4f95"/></svg>
  <span class="label">Client reviews</span>
  <h2 class="section-title">Testimonials</h2>
  <div class="quotes">
    <article class="quote">
      <div class="avatar" role="img" aria-label="Client portrait"></div>
      <div class="stars">★★★★★</div>
      <h3>JOHN SMITH</h3>
      <p>The team delivered our coin on schedule and kept us informed at every stage. Their support after launch has been quick, clear and genuinely helpful to our whole business.</p>
      <span class="quote-badge"><svg width="18" height="14" viewBox="0 0 18 14"><path d="M0 14V8C0 3 3 0 7 0v3C4 3 4 6 4 7h3v7zm11 0V8c0-5 3-8 7-8v3c-3 0-3 3-3 4h3v7z" fill="#fff"/></svg></span>
    </article>
    <article class="quote">
      <div class="avatar" role="img" aria-label="Client portrait"></div>
      <div class="stars">★★★★★</div>
      <h3>JOHN SMITH</h3>
      <p>Switching our development over was painless. They understood our existing code fast, fixed long standing issues and now ship regular updates we can rely on.</p>
      <span class="quote-badge"><svg width="18" height="14" viewBox="0 0 18 14"><path d="M0 14V8C0 3 3 0 7 0v3C4 3 4 6 4 7h3v7zm11 0V8c0-5 3-8 7-8v3c-3 0-3 3-3 4h3v7z" fill="#fff"/></svg></span>
    </article>
    <article class="quote">
      <div class="avatar" role="img" aria-label="Client portrait"></div>
      <div class="stars">★★★★★</div>
      <h3>JOHN SMITH</h3>
      <p>Fixed costs and honest advice made planning easy for us. The wallets and white paper they produced helped us win over partners and early users alike.</p>
      <span class="quote-badge"><svg width="18" height="14" viewBox="0 0 18 14"><path d="M0 14V8C0 3 3 0 7 0v3C4 3 4 6 4 7h3v7zm11 0V8c0-5 3-8 7-8v3c-3 0-3 3-3 4h3v7z" fill="#fff"/></svg></span>
    </article>
  </div>
</section>

<section class="what" id="services">
  <svg class="mini-hex" width="26" height="28" viewBox="0 0 26 28"><path d="M13 1l11 6.5v13L13 27 2 20.5v-13z" fill="#1f4f95"/></svg>
  <span class="label">Our services</span>
  <h2 class="section-title">What We Do</h2>
  <p class="what-intro">Ledgerwise Forge offers more than just development. We provide a complete solution and our clients receive access to expert advice, ongoing support, IT operations, mobile wallets, and even the creation of white papers. Our packages are tailored to suit you to match your requirements or budget, you can simply pick and choose the features you would like. Alternatively, we can create a custom package just for you.</p>
  <div class="plans">
    <div class="plan">
      <svg width="66" height="72" viewBox="0 0 66 72"><path d="M33 2l30 17v34L33 70 3 53V19z" fill="#1f4f95"/><path d="M20 44l-2-16 9 8 6-10 6 10 9-8-2 16z" stroke="#fff" stroke-width="2.5" fill="none" stroke-linejoin="round"/></svg>
      <h3>Ledgerwise Forge<br>Creation &amp; Launch</h3>
      <ul>
        <li><span class="tick"><svg width="8" height="6" viewBox="0 0 8 6"><path d="M1 3l2 2 4-4" stroke="#fff" stroke-width="1.5" fill="none"/></svg></span>This is a list item</li>
        <li><span class="tick"><svg width="8" height="6" viewBox="0 0 8 6"><path d="M1 3l2 2 4-4" stroke="#fff" stroke-width="1.5" fill="none"/></svg></span>Another list item</li>
        <li><span class="tick"><svg width="8" height="6" viewBox="0 0 8 6"><path d="M1 3l2 2 4-4" stroke="#fff" stroke-width="1.5" fill="none"/></svg></span>Yup, another list item</li>
      </ul>
      <a class="btn" href="#launch">Learn More</a>
    </div>
    <div class="plan">
      <svg width="66" height="72" viewBox="0 0 66 72"><path d="M33 2l30 17v34L33 70 3 53V19z" fill="#1f4f95"/><path d="M20 44l-2-16 9 8 6-10 6 10 9-8-2 16z" stroke="#fff" stroke-width="2.5" fill="none" stroke-linejoin="round"/></svg>
      <h3>Basic</h3>
      <ul>
        <li><span class="tick"><svg width="8" height="6" viewBox="0 0 8 6"><path d="M1 3l2 2 4-4" stroke="#fff" stroke-width="1.5" fill="none"/></svg></span>This is a list item</li>
        <li><span class="tick"><svg width="8" height="6" viewBox="0 0 8 6"><path d="M1 3l2 2 4-4" stroke="#fff" stroke-width="1.5" fill="none"/></svg></span>Another list item</li>
        <li><span class="tick"><svg width="8" height="6" viewBox="0 0 8 6"><path d="M1 3l2 2 4-4" stroke="#fff" stroke-width="1.5" fill="none"/></svg></span>Yup, another list item</li>
      </ul>
      <a class="btn" href="#basic">Learn More</a>
    </div>
    <div class="plan">
      <svg width="66" height="72" viewBox="0 0 66 72"><path d="M33 2l30 17v34L33 70 3 53V19z" fill="#1f4f95"/><path d="M20 44l-2-16 9 8 6-10 6 10 9-8-2 16z" stroke="#fff" stroke-width="2.5" fill="none" stroke-linejoin="round"/></svg>
      <h3>Mid-range</h3>
      <ul>
        <li><span class="tick"><svg width="8" height="6" viewBox="0 0 8 6"><path d="M1 3l2 2 4-4" stroke="#fff" stroke-width="1.5" fill="none"/></svg></span>This is a list item</li>
        <li><span class="tick"><svg width="8" height="6" viewBox="0 0 8 6"><path d="M1 3l2 2 4-4" stroke="#fff" stroke-width="1.5" fill="none"/></svg></span>Another list item</li>
        <li><span class="tick"><svg width="8" height="6" viewBox="0 0 8 6"><path d="M1 3l2 2 4-4" stroke="#fff" stroke-width="1.5" fill="none"/></svg></span>Yup, another list item</li>
      </ul>
      <a class="btn" href="#mid">Learn More</a>
    </div>
  </div>
</section>

<footer class="footer">
  <div class="footer-brand">
    <div class="brand"><span class="brand-mark"></span>Ledgerwise Forge</div>
    <div class="socials"><span></span><span></span><span></span><span></span></div>
  </div>
  <div class="footer-col" style="left:400px">
    <h4>Site Content</h4>
    <a href="#">Home</a><a href="#">About</a><a href="#">Feature</a><a href="#">Pricing</a><a href="#">Contact</a>
  </div>
  <div class="footer-col" style="left:580px">
    <h4>Major Topics</h4>
    <a href="#">Search</a><a href="#">T&amp;Cs</a><a href="#">Privacy</a><a href="#">Comms</a>
  </div>
  <div class="footer-col newsletter" style="left:810px">
    <h4>Get our Newsletter</h4>
    <input type="email" placeholder="Enter your email">
    <a class="btn" href="#subscribe">SUBSCRIBE</a>
  </div>
  <div class="copyright">Copyright © 2021 Ledgerwise Forge. All rights reserved.</div>
</footer>

</body>
</html>
```